Storm Restoration Contractor needs a professional letterhead design

Looking for a professional letterhead design. Not looking for your cheapo MS Word standard ones that are readily available. Dont want it to be cookie cutter look like ones readily available online. We just recently changed our logo and want to freshen up all our documents. Our company handles restoring a property back to a pre-loss condition after a storm damages it. For example, wind, hail, flood, fire losses.

Target Market(s)

Property Owners, Homeowners, Property Owners, Commercial Property Owners, Property Management Companies

Industry/Entity Type

Construction Company

Requirements
Must have
• Professional, Use 1 of 2 logo options
• Storm Restoration, Roofing, Siding, Windows

```html
<!DOCTYPE html>
<html lang="en">
<head>
<meta charset="utf-8">
<title>Stormline Restoration Letterhead</title>
<link href="https://fonts.googleapis.com/css2?family=Open+Sans:wght@400;600;700;800&display=swap" rel="stylesheet">
<style>
  :root {
    --backdrop: #d4d4d4;
    --paper: #f6f6f6;
    --brand-blue: #1f74c4;
    --ink: #3c3c3c;
    --ink-soft: #555555;
    --watermark: #e6e6e6;
  }
  * { box-sizing: border-box; margin: 0; padding: 0; }
  html, body {
    width: 1200px; height: 931px; overflow: hidden;
    background: var(--backdrop);
    font-family: "Open Sans", Arial, sans-serif;
    color: var(--ink);
  }
  .letterhead {
    position: absolute; left: 260px; top: 25px;
    width: 680px; height: 880px;
    background: var(--paper);
    overflow: hidden;
    box-shadow: 0 6px 24px rgba(0,0,0,0.18);
  }
  .brand {
    position: absolute; top: 48px; right: 110px;
    display: flex; align-items: center; gap: 10px;
  }
  .brand-dot {
    width: 34px; height: 34px; border-radius: 50%;
    background: var(--brand-blue);
  }
  .brand-name {
    font-weight: 800; font-size: 17px; letter-spacing: 1.5px;
    text-transform: uppercase; color: var(--brand-blue);
  }
  .recipient {
    position: absolute; left: 60px; top: 140px;
    font-size: 10px; line-height: 1.45; color: var(--ink-soft);
  }
  .recipient strong { color: var(--ink); font-weight: 700; }
  .letter-body {
    position: absolute; left: 60px; top: 220px; width: 545px;
    font-size: 10px; line-height: 1.55; color: var(--ink-soft);
  }
  .letter-body p { margin-bottom: 10px; }
  .signature {
    position: absolute; left: 60px; top: 548px;
    font-size: 10px; line-height: 1.4; color: var(--ink-soft);
  }
  .signature strong { color: var(--ink); font-weight: 700; }
  .watermark-ring {
    position: absolute; left: 330px; top: 640px;
    width: 260px; height: 260px; border-radius: 50%;
    border: 18px solid var(--watermark);
  }
  .contact {
    position: absolute; left: 60px; bottom: 40px;
    font-size: 10px; line-height: 1.6; color: var(--ink);
  }
  .contact .address { font-weight: 600; }
  .contact .lines { display: flex; gap: 14px; align-items: center; }
  .contact .item { display: flex; align-items: center; gap: 5px; }
  .contact svg { width: 10px; height: 10px; fill: var(--brand-blue); }
  .footer-band {
    position: absolute; left: 0; right: 0; bottom: 0; height: 18px;
    background: var(--brand-blue);
  }
</style>
</head>
<body>
  <main class="letterhead">
    <header class="brand">
      <span class="brand-dot"></span>
      <span class="brand-name">Stormline Restoration</span>
    </header>

    <address class="recipient" style="font-style:normal">
      <strong>Mr. Daniel Hart</strong><br>
      Managing Director<br>
      Northfield Holdings<br>
      1234 Main Street<br>
      USA
    </address>

    <section class="letter-body">
      <p>Lorem ipsum dolor sit amet, consectetur adipiscing elit. Nam cursus, morbi ut mi. Nullam enim leo, egestas id, condimentum at, laoreet mattis, massa. Sed eleifend nonummy diam. Praesent mauris ante, elementum et, bibendum at, posuere sit amet, nibh. Duis tincidunt lectus quis dui viverra vestibulum.</p>
      <p>Suspendisse vulputate aliquam dui. Nulla elementum dui ut augue. Aliquam vehicula mi at mauris. Maecenas placerat, nisl at consequat rhoncus, sem nunc gravida justo, quis eleifend arcu velit quis lacus. Morbi magna magna, tincidunt a, mattis non, imperdiet vitae, tellus. Sed odio est, auctor ac, sollicitudin in, consequat vitae, orci.</p>
      <p>Mauris eget eros. Pellentesque habitant morbi tristique senectus et netus et malesuada fames ac turpis egestas. In pulvinar felis nec tortor. Vivamus at justo id velit placerat pretium.</p>
      <p>Mauris nunc quam, venenatis nec, euismod sit amet, egestas placerat, est. Pellentesque habitant morbi tristique senectus et netus et malesuada fames ac turpis egestas. Cras id elit. Integer quis urna. Ut ante enim, dapibus malesuada, fringilla eu, condimentum quis, tellus. Aenean porttitor eros vel dolor.</p>
      <p>Thank you for being one of our valued customers.</p>
    </section>

    <div class="signature">
      <strong>Name Here</strong><br>
      CEO
    </div>

    <div class="watermark-ring" aria-hidden="true"></div>

    <footer class="contact">
      <div class="address">250 Harbor View Rd Ste 12, Fairview, MD 20999</div>
      <div class="lines">
        <span class="item">
          <svg viewBox="0 0 24 24"><path d="M6.6 10.8a15.1 15.1 0 0 0 6.6 6.6l2.2-2.2a1 1 0 0 1 1-.25 11.4 11.4 0 0 0 3.6.57 1 1 0 0 1 1 1V20a1 1 0 0 1-1 1A17 17 0 0 1 3 4a1 1 0 0 1 1-1h3.5a1 1 0 0 1 1 1c0 1.25.2 2.45.57 3.57a1 1 0 0 1-.25 1z"/></svg>
          555-014-2287
        </span>
        <span class="item">
          <svg viewBox="0 0 24 24"><path d="M6 3h12v5H6zM4 9h16a2 2 0 0 1 2 2v6h-4v4H6v-4H2v-6a2 2 0 0 1 2-2zm4 7v3h8v-3z"/></svg>
          555-014-3390
        </span>
        <span class="item">
          <svg viewBox="0 0 24 24"><circle cx="12" cy="12" r="10"/></svg>
          www.stormlinerestore.com
        </span>
      </div>
    </footer>

    <div class="footer-band"></div>
  </main>
</body>
</html>
```